Business Card Design for Occupational Medicine Start Up Company

We need to design a professional business card. We are a healthcare company providing occupational medicine services to blue collar industries. We are professional, efficient and high quality service providers.

Target Market(s)

Blue Collar Industry: Shipbuilding, Ports, Trucking Companies; The Executives and Safety Officers for these companies

Industry/Entity Type

Healthcare

Contact Information for Business Card

Logo, Name, Title, Email, Phone

Other font styles liked:
• Please match our Brand Guide

Requirements
Must have
• Our Company Colors and Logo

```html
<!DOCTYPE html>
<html lang="en">
<head>
<meta charset="utf-8">
<title>CrewWell Clinics — Business Card</title>
<link rel="stylesheet" href="https://fonts.googleapis.com/css2?family=Poppins:wght@300;400;500;700&display=swap">
<style>
  :root {
    --stage: #141414;
    --paper: #ffffff;
    --navy: #2a3285;
    --royal: #2f3a92;
    --sky: #2aa6df;
    --amber: #f4a93a;
    --ink: #3a3a3a;
    --white: #ffffff;
  }
  * { margin: 0; padding: 0; box-sizing: border-box; }
  html, body { width: 1200px; height: 820px; overflow: hidden; }
  body {
    background: var(--stage);
    font-family: "Poppins", sans-serif;
    position: relative;
  }
  .card {
    position: absolute;
    top: 255px;
    width: 540px;
    height: 310px;
    overflow: hidden;
  }
  .card--front {
    left: 40px;
    background: var(--paper);
    border-left: 3px solid var(--amber);
    border-bottom: 3px solid var(--amber);
    color: var(--ink);
  }
  .card--back {
    left: 620px;
    background: var(--royal);
    border-left: 3px solid var(--amber);
    border-bottom: 3px solid var(--amber);
  }
  .brand {
    position: absolute;
    display: flex;
    align-items: center;
    gap: 14px;
  }
  .card--front .brand { left: 150px; top: 62px; }
  .brand__dot {
    width: 46px; height: 46px;
    border-radius: 50%;
    background: var(--sky);
    flex: none;
  }
  .brand__name {
    font-weight: 700;
    font-size: 25px;
    letter-spacing: 0.5px;
    line-height: 1;
    color: var(--navy);
    text-transform: uppercase;
    white-space: nowrap;
  }
  .card--back .brand { right: 34px; top: 132px; }
  .card--back .brand__name { color: var(--white); font-size: 24px; }
  .rule {
    position: absolute;
    height: 1px;
    background: var(--navy);
  }
  .rule--wide { left: 40px; right: 40px; top: 160px; }
  .rule--short { left: 40px; width: 150px; top: 232px; }
  .person { position: absolute; left: 40px; top: 182px; }
  .person__name {
    font-size: 20px;
    line-height: 1.1;
    color: var(--navy);
    font-weight: 300;
    text-transform: uppercase;
  }
  .person__name strong { font-weight: 700; }
  .person__title { font-size: 14px; color: var(--ink); font-weight: 400; }
  .contact {
    position: absolute;
    left: 40px;
    top: 242px;
    list-style: none;
    font-size: 13px;
    line-height: 19px;
  }
  .contact li { display: flex; align-items: center; gap: 8px; white-space: nowrap; }
  .contact svg { width: 12px; height: 12px; fill: var(--navy); flex: none; }
  .contact .accent { color: var(--sky); }
  .address {
    position: absolute;
    right: 40px;
    top: 176px;
    text-align: right;
    font-size: 13px;
    line-height: 18px;
    white-space: nowrap;
  }
</style>
</head>
<body>
  <section class="card card--front">
    <div class="brand">
      <span class="brand__dot"></span>
      <span class="brand__name">CrewWell Clinics</span>
    </div>
    <div class="rule rule--wide"></div>
    <div class="person">
      <p class="person__name"><strong>Daniel</strong> Hart</p>
      <p class="person__title">Managing Director</p>
    </div>
    <div class="rule rule--short"></div>
    <ul class="contact">
      <li>
        <svg viewBox="0 0 24 24" aria-hidden="true"><path d="M6.6 10.8a15 15 0 0 0 6.6 6.6l2.2-2.2a1 1 0 0 1 1-.25 11.4 11.4 0 0 0 3.6.57 1 1 0 0 1 1 1V20a1 1 0 0 1-1 1A17 17 0 0 1 3 4a1 1 0 0 1 1-1h3.5a1 1 0 0 1 1 1c0 1.25.2 2.45.57 3.57a1 1 0 0 1-.25 1z"/></svg>
        055-210 384 617
      </li>
      <li>
        <svg viewBox="0 0 24 24" aria-hidden="true"><path d="M2 5h20v14H2zm2 2v.5l8 5 8-5V7z"/></svg>
        hello@crewwell.com
      </li>
      <li>
        <svg viewBox="0 0 24 24" aria-hidden="true"><path d="M12 2a10 10 0 1 0 0 20 10 10 0 0 0 0-20zm6.9 9h-3a15 15 0 0 0-1.3-6A8 8 0 0 1 18.9 11zM12 4c.9 1.3 1.7 3.8 1.9 7h-3.8c.2-3.2 1-5.7 1.9-7zM9.4 5a15 15 0 0 0-1.3 6h-3A8 8 0 0 1 9.4 5zM5.1 13h3a15 15 0 0 0 1.3 6A8 8 0 0 1 5.1 13zM12 20c-.9-1.3-1.7-3.8-1.9-7h3.8c-.2 3.2-1 5.7-1.9 7zm2.6-1a15 15 0 0 0 1.3-6h3a8 8 0 0 1-4.3 6z"/></svg>
        <span>www.<span class="accent">crewwellcare</span>.com</span>
      </li>
    </ul>
    <p class="address">88 Harbor Works Road, Unit 4<br>30417, Eastport Bay</p>
  </section>

  <section class="card card--back">
    <div class="brand">
      <span class="brand__name">CrewWell Clinics</span>
    </div>
  </section>
</body>
</html>
```